Hi everyone,
Fresh Walls Co is a business that renovates older houses into modern homes. I'm looking for a design that is clean and simple. It needs to show the client that renovating is a simple process. No more than 3 colours to be used thanks.

What I need:
1. Logo
2. Business card (one side)
3. Letter head (A4)

Looking forward to the designs!

Construction

Fresh Walls Co

Sans Serif

Must have
• Trading name: Fresh Walls Co
• Contact name: Declan Ashworth
• Email: declanashworth@freshwallsco.example.com.au
• Tel: 0412 758 204
• Clean and simple
Nice to have
• If design might include a few tools. eg Hammer, paint roller etc.
Should not have
• Complicated design

```html
<!DOCTYPE html>
<html lang="en">
<head>
<meta charset="utf-8">
<title>Fresh Walls Co — Business Card</title>
<link rel="stylesheet" href="https://fonts.googleapis.com/css2?family=Roboto+Condensed:wght@400;700&display=swap">
<style>
  :root {
    --brand-blue: #1f74bd;
    --brand-orange: #f7931e;
    --card-white: #ffffff;
    --backdrop: #e9ebee;
  }
  * { margin: 0; padding: 0; box-sizing: border-box; }
  html, body {
    width: 1200px;
    height: 800px;
    overflow: hidden;
    background: var(--backdrop);
    font-family: "Roboto Condensed", sans-serif;
  }
  .business-card {
    position: absolute;
    left: 100px;
    top: 95px;
    width: 1000px;
    height: 611px;
    background: var(--card-white);
    overflow: hidden;
    box-shadow: 0 6px 24px rgba(0, 0, 0, 0.15);
  }
  .card-swoosh {
    position: absolute;
    inset: 0;
    width: 100%;
    height: 100%;
  }
  .swoosh-panel { fill: var(--brand-blue); }
  .swoosh-stripe { fill: var(--brand-orange); }

  .brand-mark {
    position: absolute;
    left: 60px;
    top: 215px;
    display: flex;
    align-items: center;
    gap: 18px;
  }
  .brand-dot {
    width: 56px;
    height: 56px;
    border-radius: 50%;
    background: var(--brand-orange);
    flex: none;
  }
  .brand-name {
    font-weight: 700;
    font-size: 56px;
    line-height: 1;
    color: var(--brand-orange);
    white-space: nowrap;
  }

  .contact-block {
    position: absolute;
    right: 40px;
    top: 380px;
    color: var(--card-white);
    text-align: right;
  }
  .contact-row {
    display: flex;
    justify-content: flex-end;
    align-items: center;
    gap: 16px;
    white-space: nowrap;
  }
  .contact-name {
    font-weight: 700;
    font-size: 44px;
    letter-spacing: 0.5px;
    text-transform: uppercase;
    line-height: 1.15;
    margin-bottom: 6px;
  }
  .contact-email {
    font-weight: 400;
    font-size: 23px;
    line-height: 1.5;
  }
  .contact-phone {
    font-weight: 400;
    font-size: 28px;
    line-height: 1.4;
  }
  .contact-icon {
    width: 42px;
    height: 30px;
    flex: none;
  }
  .contact-icon path { fill: none; stroke: var(--card-white); stroke-width: 2.6; stroke-linejoin: round; stroke-linecap: round; }
  .contact-icon .solid { fill: var(--card-white); stroke: none; }
</style>
</head>
<body>
  <article class="business-card">
    <svg class="card-swoosh" viewBox="0 0 1000 611" preserveAspectRatio="none" aria-hidden="true">
      <path class="swoosh-panel" d="M1000 90 Q 520 230 290 611 L 1000 611 Z"/>
      <path class="swoosh-stripe" d="M1000 40 Q 500 160 300 500 Q 520 185 1000 62 Z"/>
    </svg>

    <div class="brand-mark">
      <span class="brand-dot"></span>
      <span class="brand-name">Fresh Walls Co</span>
    </div>

    <div class="contact-block">
      <div class="contact-row">
        <span class="contact-name">Declan Ashworth</span>
      </div>
      <div class="contact-row">
        <span class="contact-email">declanashworth@freshwallsco.example.com.au</span>
        <svg class="contact-icon" viewBox="0 0 42 30" aria-label="Email">
          <path d="M3 3 H39 V27 H3 Z"/>
          <path d="M3 3 L21 17 L39 3"/>
        </svg>
      </div>
      <div class="contact-row">
        <span class="contact-phone">0412 758 204</span>
        <svg class="contact-icon" viewBox="0 0 42 30" aria-label="Phone">
          <path class="solid" d="M14 2 C10 4 8 8 9 13 C11 21 18 27 26 28 C30 29 33 27 34 24 L28 19 C26 20 25 22 23 21 C19 19 16 15 15 12 C15 10 17 9 18 7 Z"/>
        </svg>
      </div>
    </div>
  </article>
</body>
</html>
```